Event flyer for Sunday night Youth Group

Need a 4 x 6 or 5 x 7 flyer for a new youth group starting on April 14. The youth group is for students in middle school and high school so it needs to look fun and cool, but not childish. I prefer it not to include pictures of people unless it's so obscure you can't really see their faces. I've uploaded some pictures of flyers I like. I've also attached a couple versions of our logo to use on the flyer.
Information the flyer needs to include:
Youth Group
Sundays, 6-8pm (beginning April 14)
Location: Marlowe's - 4219 Quarry Fern Ave N, Keizer, 97318
There will be dinner, games, friends, and a message.
Target Market(s)
Youth ages 13-18
Industry/Entity Type
Church
Font styles to use
Colors
Designer to choose colors to be used in the design.
Look and feel

```html
<!DOCTYPE html>
<html lang="en">
<head>
<meta charset="utf-8">
<title>Youth Group Flyer</title>
<link href="https://fonts.googleapis.com/css2?family=Bebas+Neue&family=Kaushan+Script&family=Montserrat:wght@400;500;600;700;800&display=swap" rel="stylesheet">
<style>
  :root {
    --stage: #9b9b9b;
    --night: #0c1f29;
    --night-teal: #1d4a52;
    --slate: #2c4a52;
    --sage: #7f9580;
    --sage-light: #a3b2a2;
    --gold: #f6b62f;
    --orange: #f07a24;
    --paper: #f6f6f4;
    --ink: #1f2e33;
    --white: #ffffff;
  }
  * { margin: 0; padding: 0; box-sizing: border-box; }
  html, body { width: 1200px; height: 2430px; overflow: hidden; }
  body { background: var(--stage); position: relative; font-family: "Montserrat", sans-serif; }

  .flyer {
    position: absolute; left: 50px; top: 445px;
    width: 990px; height: 1385px;
    transform: scale(1.1111); transform-origin: top left;
    overflow: hidden;
    box-shadow: 0 20px 40px rgba(0,0,0,.35);
  }
  .night-scene {
    position: absolute; inset: 0 0 420px 0;
    background:
      radial-gradient(ellipse 60% 45% at 50% 30%, #2a5d63 0%, rgba(29,74,82,.6) 40%, transparent 75%),
      linear-gradient(180deg, #0a1a22 0%, var(--night-teal) 45%, #123038 80%, var(--night) 100%);
  }
  .brand {
    position: absolute; top: 60px; left: 0; right: 0;
    display: flex; justify-content: center; align-items: center; gap: 14px;
  }
  .brand-mark { width: 34px; height: 34px; background: var(--white); }
  .brand-name {
    color: var(--white); font-weight: 500; font-size: 34px; letter-spacing: 2px; line-height: 1;
  }
  .rings { position: absolute; left: 0; top: 0; width: 990px; height: 940px; }
  .title-script {
    position: absolute; left: 0; right: 0; top: 285px; text-align: center;
    font-family: "Kaushan Script", cursive; font-size: 210px; line-height: 1;
    background: linear-gradient(180deg, var(--gold) 20%, var(--orange) 85%);
    -webkit-background-clip: text; background-clip: text; color: transparent;
    z-index: 2; transform: rotate(-4deg);
  }
  .title-block {
    position: absolute; left: 0; right: 0; top: 440px; text-align: center;
    font-family: "Bebas Neue", sans-serif; font-size: 300px; line-height: 1; letter-spacing: -4px;
    color: var(--white); z-index: 1;
  }
  .paper {
    position: absolute; left: 0; right: 0; bottom: 0; height: 445px;
    background:
      radial-gradient(ellipse at 20% 70%, #e6e7e5 0%, transparent 55%),
      radial-gradient(ellipse at 85% 30%, #ececea 0%, transparent 50%),
      var(--paper);
  }
  .torn-edge { position: absolute; left: 0; top: 925px; width: 990px; height: 40px; }
  .photo {
    position: absolute; top: 770px; width: 250px; height: 250px; border-radius: 50%;
    border: 7px solid var(--sage);
  }
  .photo-friends { left: 69px; background: linear-gradient(180deg, #4a5866 0%, #b77a45 55%, #2a1d18 100%); }
  .photo-gathering { left: 371px; background: linear-gradient(180deg, #8a6142 0%, #3a2a28 50%, #5a2525 100%); }
  .photo-worship { left: 666px; background: linear-gradient(180deg, #f2b45a 0%, #e08a2c 50%, #4a2510 100%); }

  .time-box {
    position: absolute; left: 67px; top: 1046px; width: 141px; height: 155px;
    background: var(--slate); color: var(--white);
    font-weight: 700; font-size: 50px; line-height: 1; text-align: center; padding-top: 12px;
  }
  .time-box .to {
    display: block; width: 44px; height: 44px; margin: -2px auto -4px; border-radius: 50%;
    background: var(--orange); font-family: "Kaushan Script", cursive; font-size: 30px;
    line-height: 42px; font-weight: 400; position: relative; z-index: 1;
  }
  .day {
    position: absolute; left: 229px; top: 1040px;
    font-weight: 800; font-size: 96px; line-height: 1; color: var(--slate); letter-spacing: -3px;
  }
  .divider { position: absolute; left: 636px; top: 1053px; width: 3px; height: 78px; background: var(--slate); }
  .start { position: absolute; left: 680px; top: 1046px; }
  .start-label { font-weight: 500; font-size: 28px; letter-spacing: 7px; color: var(--ink); line-height: 1; }
  .start-date { font-weight: 700; font-size: 50px; color: var(--sage); line-height: 1; margin-top: 8px; letter-spacing: -1px; }
  .start-date sup { font-size: 26px; vertical-align: 18px; }
  .venue {
    position: absolute; left: 222px; top: 1147px; width: 704px; height: 54px;
    background: var(--slate); color: var(--white); border-radius: 3px;
    font-size: 24px; font-weight: 500; line-height: 54px; text-align: center;
  }
  .venue strong { color: var(--gold); font-weight: 700; }
  .there { position: absolute; left: 71px; top: 1232px; color: var(--slate); line-height: .9; }
  .there-big { font-family: "Bebas Neue", sans-serif; font-size: 66px; display: block; }
  .there-small { font-size: 29px; font-weight: 500; color: var(--ink); display: block; }
  .offers { position: absolute; left: 226px; top: 1222px; display: flex; gap: 20px; align-items: center; list-style: none; }
  .offer { display: flex; align-items: center; gap: 10px; font-size: 23px; font-weight: 500; color: var(--ink); }
  .offer-icon { width: 44px; height: 44px; }
  .site {
    position: absolute; left: 226px; top: 1286px; width: 703px; height: 42px;
    border: 2px solid var(--slate); border-radius: 3px;
    font-size: 27px; letter-spacing: 4px; text-align: center; line-height: 38px; color: var(--ink);
  }
  .site strong { color: var(--slate); font-weight: 700; }
</style>
</head>
<body>
  <article class="flyer">
    <div class="night-scene" role="img" aria-label="Dark teal night sky with silhouetted crowd raising hands and scattered sparkles"></div>

    <header class="brand">
      <span class="brand-mark"></span>
      <span class="brand-name">HARBORVIEW FELLOWSHIP</span>
    </header>

    <svg class="rings" viewBox="0 0 990 940" aria-hidden="true">
      <g fill="none" stroke="#b8d47a" stroke-opacity=".7">
        <circle cx="500" cy="470" r="290" stroke-width="2"/>
        <circle cx="506" cy="466" r="300" stroke-width="1.5"/>
        <circle cx="494" cy="476" r="282" stroke-width="1"/>
        <circle cx="502" cy="462" r="305" stroke-width="1" stroke-opacity=".4"/>
      </g>
    </svg>

    <h1>
      <span class="title-script">Youth</span>
      <span class="title-block">GROUP</span>
    </h1>

    <section class="paper"></section>
    <svg class="torn-edge" viewBox="0 0 990 40" preserveAspectRatio="none" aria-hidden="true">
      <polygon fill="#7f9580" points="0,22 40,18 90,24 140,16 200,22 260,14 330,20 400,15 470,22 540,14 610,21 680,13 750,20 820,15 890,22 950,16 990,20 990,40 0,40"/>
      <polygon fill="#f6f6f4" points="0,28 45,24 95,30 150,22 210,28 270,21 340,27 410,22 480,29 550,21 620,28 690,20 760,27 830,22 900,29 955,23 990,27 990,40 0,40"/>
    </svg>

    <div class="photo photo-friends" role="img" aria-label="Silhouetted friends holding hands raised at sunset"></div>
    <div class="photo photo-gathering" role="img" aria-label="Congregation gathered in a warmly lit church"></div>
    <div class="photo photo-worship" role="img" aria-label="Crowd raising hands in golden stage light"></div>

    <div class="time-box">6PM<span class="to">to</span>8PM</div>
    <div class="day">SUNDAY</div>
    <div class="divider"></div>
    <div class="start">
      <div class="start-label">BEGINNING</div>
      <div class="start-date">APRIL 14<sup>TH</sup></div>
    </div>
    <div class="venue"><strong>MARLOWE'S</strong> - 4219 QUARRY FERN AVE N, KEIZER, 97318</div>

    <div class="there"><span class="there-big">THERE</span><span class="there-small">WILL BE</span></div>
    <ul class="offers">
      <li class="offer">
        <svg class="offer-icon" viewBox="0 0 44 44" aria-hidden="true"><circle cx="22" cy="22" r="20" fill="#a3b2a2" stroke="#2c4a52" stroke-width="2"/><path d="M11 27 a11 11 0 0 1 22 0 z" fill="#2c4a52"/><rect x="9" y="28" width="26" height="3" fill="#2c4a52"/><circle cx="22" cy="15" r="2" fill="#2c4a52"/></svg>
        Dinner
      </li>
      <li class="offer">
        <svg class="offer-icon" viewBox="0 0 44 44" aria-hidden="true"><circle cx="22" cy="22" r="20" fill="#a3b2a2" stroke="#2c4a52" stroke-width="2"/><rect x="10" y="16" width="24" height="13" rx="6" fill="#2c4a52"/><rect x="14" y="21" width="6" height="2" fill="#a3b2a2"/><rect x="16" y="19" width="2" height="6" fill="#a3b2a2"/><circle cx="27" cy="21" r="1.5" fill="#a3b2a2"/><circle cx="29" cy="24" r="1.5" fill="#a3b2a2"/></svg>
        Games
      </li>
      <li class="offer">
        <svg class="offer-icon" viewBox="0 0 44 44" aria-hidden="true"><circle cx="22" cy="22" r="20" fill="#a3b2a2" stroke="#2c4a52" stroke-width="2"/><circle cx="17" cy="16" r="4" fill="#2c4a52"/><circle cx="27" cy="16" r="4" fill="#2c4a52"/><path d="M10 31 v-5 a5 5 0 0 1 14 0 v5 z M20 31 v-5 a5 5 0 0 1 14 0 v5 z" fill="#2c4a52"/></svg>
        Friends
      </li>
      <li class="offer">
        <svg class="offer-icon" viewBox="0 0 44 44" aria-hidden="true"><circle cx="22" cy="22" r="20" fill="#a3b2a2" stroke="#2c4a52" stroke-width="2"/><path d="M22 10 L16 24 L13 32 H21 Z M22 10 L28 24 L31 32 H23 Z" fill="#2c4a52"/></svg>
        And a message
      </li>
    </ul>
    <div class="site">www.<strong>harborview-fellowship</strong>.church</div>
  </article>
</body>
</html>
```